Website design for a hair building fibre

Hi I’m needing a website made for both men and women to purchase the product is a hair building fibre that you apply to thinning hair to make your hair look really thick I’ll need the website to be easy to use professional and also very classy I will need it to work with lumen split tok fund and credit cards I’ll need to have the CEO words and everything ready so I can sell I don’t have photos that I want to put on there so I’ll need a website designer to assist me in having the beautiful photos on there I know very little about websites so I need someone to be able to do it all for me

I can only provide photos of the colours of the products
I believe there will be 8 colours to sell as well
I’ve uploaded a photo of the logo I’d really like it if the website designer can check other competitors website so my website does not look like theres, I don’t want my website to look like a copied website of the competitors I’m located in Australia.
I’m also looking for someone who can open up a Palvista and Glimmerly page and then can unload photos on them ready for consumers to view and buy.

```html
<!DOCTYPE html>
<html lang="en">
<head>
<meta charset="utf-8">
<title>Densora – Hair Building Fibre – Theme Variations</title>
<link href="https://fonts.googleapis.com/css2?family=Montserrat:wght@300;400;600;700&family=Roboto:wght@400;500;700&display=swap" rel="stylesheet">
<style>
:root{
  --navy:#121826;
  --navy-deep:#0d121c;
  --blue:#6cb8e0;
  --white:#ffffff;
  --canvas:#ffffff;
  --card-dark:#161d2b;
  --head-font:"Montserrat",sans-serif;
  --body-font:"Roboto",sans-serif;
}
*{box-sizing:border-box;margin:0;padding:0}
html,body{width:1079px;height:1200px;overflow:hidden;background:var(--canvas);font-family:var(--body-font)}
.board{position:relative;width:1079px;height:1200px}

.page{position:absolute;top:43px;width:296px;height:1121px;overflow:hidden;background:var(--surface);color:var(--ink)}
.page-1{left:58px}.page-2{left:395px}.page-3{left:731px}
.theme-dark{--surface:#121826;--band:rgba(0,0,0,.18);--ink:#ffffff;--muted:#b8bfcb;--card:#141b28;--card-line:#1e2636;--accent-head:var(--blue)}
.theme-light{--surface:#e3e4e6;--band:rgba(0,0,0,.035);--ink:#1b2230;--muted:#3d4452;--card:#e8e9eb;--card-line:#c9cbcf;--accent-head:var(--ink)}
.theme-gold{--surface:linear-gradient(180deg,#a98526 0%,#b8962f 30%,#c8b243 55%,#d8d35c 78%,#e1dd6c 100%);--band:rgba(255,255,255,.05);--ink:#1b2230;--muted:#2f3440;--card:rgba(0,0,0,.04);--card-line:rgba(0,0,0,.18);--accent-head:var(--ink)}

.page-shapes{position:absolute;inset:0;width:296px;height:1121px}
.abs{position:absolute}

/* top bar & nav */
.topbar{position:absolute;left:0;top:0;width:296px;height:10px;background:var(--blue);color:var(--white);font-size:2.8px;font-weight:700;display:flex;align-items:center;justify-content:space-between;padding:0 27px}
.topbar-links{display:flex;gap:6px}
.mainnav{position:absolute;left:0;top:10px;width:296px;height:19px;background:var(--navy);display:flex;align-items:center;padding:0 27px;color:var(--white)}
.logo{display:flex;flex-direction:column;line-height:1}
.logo b{font-family:var(--head-font);font-weight:300;font-size:7px;letter-spacing:.2px}
.logo small{font-size:2px;letter-spacing:.4px;color:var(--blue);margin-top:1px}
.menu{display:flex;gap:5.5px;margin-left:auto;font-size:2.9px;font-weight:700}
.menu .active{color:var(--blue)}
.nav-icon{width:7px;height:7px;border-radius:50%;margin-left:5px;border:.6px solid var(--blue)}
.nav-icon.search{background:var(--blue);margin-left:12px}

/* hero */
.hero-photo{left:27px;top:35px;width:120px;height:120px;border-radius:4px;background:radial-gradient(ellipse at 55% 40%,#4a3a33 0%,#231c1d 45%,#121826 80%)}
.hero-title{left:150px;top:56px;font-family:var(--head-font);font-weight:400;font-size:9.6px;line-height:13.5px;color:var(--white);letter-spacing:.1px}
.hero-title em{font-style:normal;color:var(--blue)}
.hero-text{left:151px;top:109px;width:120px;font-size:4px;line-height:5.8px;color:var(--white)}
.btn{position:absolute;background:var(--blue);color:var(--white);border-radius:8px;font-size:2.7px;font-weight:700;display:flex;align-items:center;justify-content:center;gap:2px;letter-spacing:.2px}
.btn::after{content:"";width:2.2px;height:2.2px;border-radius:50%;background:var(--white)}
.hero-btn{left:151px;top:128px;width:45px;height:11px}
.hero-product{left:224px;top:128px;width:40px;height:45px;border-radius:2px;background:linear-gradient(90deg,#2a2d33,#5c6068 30%,#c9ccd1 50%,#3a3d44 70%,#1e2025)}
.best-badge{left:257px;top:125px;width:13px;height:13px;border-radius:50%;background:var(--blue);border:.8px solid var(--white)}

/* section titles */
.sec-title{position:absolute;left:0;width:296px;text-align:center;font-family:var(--head-font);font-weight:400;font-size:7.8px;color:var(--ink);letter-spacing:.1px}
.sec-title .hl{color:var(--accent-head)}
.sec-title .blue{color:var(--blue)}

/* products */
.products{position:absolute;left:36px;top:228px;width:224px;display:flex;gap:3.5px}
.product-card{flex:1;height:78px;background:var(--card);border:.5px solid var(--card-line);display:flex;flex-direction:column;align-items:center;padding-top:5px}
.product-card.is-hover{box-shadow:0 0 4px rgba(0,0,0,.35)}
.can{width:9px;height:30px;border-radius:1.5px 1.5px 1px 1px;background:linear-gradient(90deg,#1a1c20,#55585f 45%,#1a1c20)}
.can.silver{background:linear-gradient(90deg,#9fa3a9,#f2f3f5 45%,#9fa3a9)}
.can.plum{background:linear-gradient(90deg,#201621,#5a3b56 45%,#201621)}
.can.graphite{background:linear-gradient(90deg,#25272b,#63666c 45%,#25272b)}
.p-title{font-size:3.6px;font-weight:700;color:var(--ink);margin-top:5px}
.theme-light .p-title{color:#fff;text-shadow:0 0 .4px #9aa}
.p-price{font-family:var(--head-font);font-size:6.4px;font-weight:600;color:var(--blue);margin-top:1px}
.swatches{display:flex;gap:.6px;margin-top:2px}
.swatches i{width:4px;height:4px;border-radius:50%;border:.4px solid #777}
.sw1{background:#0c0c0c}.sw2{background:#4b2c1c}.sw3{background:#7a1f1f}.sw4{background:#2d1a14}.sw5{background:#444}.sw6{background:#1f3329}
.shop-btn{margin-top:6px;width:25px;height:5px;border-radius:3px;background:#1a202c;border:.4px solid #8a93a3;color:#fff;font-size:2px;font-weight:700;display:flex;align-items:center;justify-content:center}
.is-hover .shop-btn{background:var(--blue);border-color:var(--blue)}
.quick-icons{position:absolute;left:198px;top:231px;width:6px;height:17px;display:flex;flex-direction:column;gap:1px}
.quick-icons i{height:5px;background:#1d2433;border-radius:1px}
.theme-light .quick-icons i{background:#d3d5d9}
.view-all{left:121px;top:318px;width:54px;height:11px}

/* steps */
.steps{position:absolute;left:30px;top:419px;width:236px;display:flex;justify-content:space-between}
.step{width:72px;display:flex;flex-direction:column;align-items:center;position:relative}
.step-ring{width:49px;height:49px;border-radius:50%;border:3px solid var(--blue);background:var(--navy);box-shadow:0 0 0 1.5px var(--white) inset;display:flex;align-items:center;justify-content:center}
.step-num{position:absolute;left:8px;top:1px;width:9px;height:9px;border-radius:50%;background:var(--blue);border:.7px solid var(--white);color:#fff;font-size:3px;font-weight:700;display:flex;align-items:center;justify-content:center}
.step h3{font-size:3.6px;font-weight:700;color:var(--ink);margin-top:9px;white-space:nowrap}
.step p{font-size:2.9px;line-height:4.4px;color:var(--muted);text-align:center;margin-top:3px;width:62px}

/* conceal */
.videos{position:absolute;left:27px;top:561px;width:242px;display:flex;gap:8px}
.video-card{flex:1;height:96px;background:var(--card-dark);position:relative;display:flex;flex-direction:column;align-items:center}
.theme-dark .video-card{background:#171e2c}
.video-card .btn{position:relative;width:52px;height:9px;margin-top:8px}
.video-card h3{font-family:var(--body-font);font-weight:400;color:#fff;font-size:7.2px;line-height:9.6px;text-align:center;margin-top:3px}
.video-card h3 b{font-weight:700}
.ba-labels{width:100%;display:flex;justify-content:space-around;font-size:3.6px;font-weight:700;color:#fff;margin-top:3px}
.ba-photo{position:absolute;left:0;bottom:0;width:100%;height:37px;background:linear-gradient(90deg,#3b2a22,#a17a62 25%,#2e221c 50%,#b08a70 75%,#3b2a22)}
.ba-photo.men{background:linear-gradient(90deg,#1b2130,#c9a48a 25%,#e8e8ea 45%,#c49b7e 75%,#e9e9eb)}

/* about */
.about-title{left:27px;top:696px;font-family:var(--head-font);font-size:8px;color:var(--ink)}
.about-title .blue{color:var(--blue)}
.theme-light .about-title .blue,.theme-gold .about-title .blue{color:var(--ink)}
.about-text{left:27px;top:711px;width:118px;font-size:2.9px;line-height:6.3px;color:var(--muted);text-align:justify}
.learn-btn{left:27px;top:769px;width:41px;height:11px}
.about-photo{left:160px;top:692px;width:108px;height:89px;background:radial-gradient(ellipse at 45% 40%,#6b5243 0%,#2b211d 40%,#3d3a3b 75%,#55524f)}

/* testimonials */
.quotes{position:absolute;left:30px;top:833px;width:238px;display:flex;gap:11px}
.quote{flex:1;height:30px;border-radius:4px;background:var(--card);box-shadow:1px 1px 2px rgba(0,0,0,.3);font-size:2.8px;line-height:5.8px;font-style:italic;color:var(--muted);padding:6px 4px 0;position:relative}
.theme-dark .quote{background:#151c29}
.theme-light .quote{background:#eceded}
.theme-gold .quote{background:rgba(255,255,255,.08)}
.quote.featured{background:var(--blue)!important;color:#dbeef9}
.quote::after{content:"\201C\201C";position:absolute;right:5px;bottom:1px;font-size:7px;font-weight:700;color:var(--blue);font-style:normal;letter-spacing:-1px}
.quote.featured::after{color:#1a2b45}
.authors{position:absolute;left:30px;top:869px;width:238px;display:flex;gap:11px}
.author{flex:1;display:flex;align-items:center;gap:4px;padding-left:2px}
.avatar{width:13px;height:13px;border-radius:50%;background:radial-gradient(circle at 50% 40%,#c49778,#6f4c39)}
.author b{display:block;font-size:2.9px;color:var(--ink)}
.author small{font-size:2.6px;color:var(--muted)}

/* thicker */
.thick-text{left:40px;top:975px;width:216px;text-align:center;font-size:3.4px;line-height:5.8px;color:var(--muted)}

/* footer */
.foot-logo{left:27px;top:1052px}
.foot-logo b{font-family:var(--head-font);font-weight:300;font-size:11px;color:#fff;display:block;letter-spacing:.3px}
.foot-logo small{font-size:3px;color:var(--blue);letter-spacing:.6px}
.payments{left:40px;top:1076px;display:flex;gap:1.5px;align-items:center;background:#e9edf3;padding:1px 2px;border-radius:1px}
.payments span{font-size:2.1px;font-weight:700;color:#1b2230}
.payments i{width:3.5px;height:2.6px;background:#3b5b9a}
.foot-col{position:absolute;top:1045px;color:#fff;font-size:2.8px}
.foot-col h4{font-size:2.8px;font-weight:700;margin-bottom:2px}
.foot-col h4::after{content:"";display:block;width:10px;height:.5px;background:var(--blue);margin-top:2px}
.foot-col li{list-style:none;line-height:7.4px;padding-left:6px;position:relative}
.foot-col li::before{content:"»";position:absolute;left:0;color:var(--blue)}
.foot-col.contact li::before{content:"";top:2px;width:3.5px;height:3.5px;border-radius:50%;background:#d6dbe3}
.col-links{left:102px}.col-contact{left:145px;width:58px}.col-subscribe{left:204px;width:66px}
.col-contact li{line-height:3.6px;padding:1.5px 0 2.2px 8px}
.col-subscribe p{font-size:2.8px;line-height:4.3px;color:#d4d8df}
.email-field{margin-top:4px;height:9px;border-radius:5px;background:#fff;display:flex;align-items:center;justify-content:space-between;padding-left:7px;color:#8a93a3;font-size:2.4px;overflow:hidden}
.email-field i{width:11px;height:9px;background:var(--blue)}
.socials{display:flex;gap:2px;margin-top:4px}
.socials i{width:6.5px;height:6.5px;border-radius:50%;background:#d6dbe3}
.socials i.on{background:var(--blue)}
.copyright{position:absolute;left:0;bottom:0;width:296px;height:13px;background:var(--blue);color:#fff;font-size:2.9px;display:flex;align-items:center;justify-content:center}
</style>
</head>
<body>
<main class="board">

<!-- ===== Theme: dark navy ===== -->
<section class="page page-1 theme-dark">
  <svg class="page-shapes" viewBox="0 0 296 1121" aria-hidden="true">
    <rect y="518" width="296" height="155" fill="var(--band)"/>
    <rect y="941" width="296" height="90" fill="var(--band)"/>
    <path d="M0 0H296V150C200 152 90 172 0 210Z" fill="var(--navy)"/>
    <path d="M0 210C55 184 110 168 150 163" stroke="var(--blue)" stroke-width="2.4" fill="none"/>
    <path d="M0 388C100 386 220 362 296 330" stroke="var(--blue)" stroke-width="2" fill="none"/>
    <path d="M0 811C70 772 170 759 296 756" stroke="var(--blue)" stroke-width="2" fill="none"/>
    <path d="M0 1035C120 1030 230 1002 296 972V1121H0Z" fill="var(--navy)"/>
    <path d="M0 1035C120 1030 230 1002 296 972" stroke="var(--blue)" stroke-width="2" fill="none"/>
  </svg>
  <div class="topbar"><span>Spend $60 or more to receive free standard shipping</span><nav class="topbar-links"><span>Login</span><span>My Account</span><span>Checkout</span><span>Wishlist</span></nav></div>
  <header class="mainnav"><div class="logo"><b>DENSORA</b><small>HAIR BUILDING FIBRE</small></div><nav class="menu"><span class="active">Home</span><span>About</span><span>Shop</span><span>Offers</span><span>How It Works</span><span>FAQ</span><span>Contact</span></nav><span class="nav-icon search"></span><span class="nav-icon cart"></span></header>
  <div class="abs hero-photo" role="img" aria-label="Photo of a glamorous couple with full, thick hair"></div>
  <h1 class="abs hero-title">HAIR - BUILDING FIBRE<br>FOR <em>THICKER , FULLER</em><br>HAIR</h1>
  <p class="abs hero-text">Lorem ipsum dolor sit amet, consectetur adipiscing elit, sed do eiusmod tempor incididunt ut labore</p>
  <span class="btn hero-btn">PURCHASE NOW</span>
  <div class="abs hero-product" role="img" aria-label="Product shot of hair fibre bottles and spray"></div>
  <span class="abs best-badge"></span>
  <h2 class="sec-title" style="top:209px">FEATURED <span class="blue">PRODUCTS</span></h2>
  <div class="products">
    <div class="product-card"><i class="can"></i><span class="p-title">Product Title</span><span class="p-price">$30.00</span><span class="swatches"><i class="sw1"></i><i class="sw2"></i><i class="sw3"></i><i class="sw4"></i><i class="sw5"></i><i class="sw6"></i></span><span class="shop-btn">SHOP NOW</span></div>
    <div class="product-card"><i class="can silver"></i><span class="p-title">Product Title</span><span class="p-price">$30.00</span><span class="swatches"><i class="sw1"></i><i class="sw2"></i><i class="sw3"></i><i class="sw4"></i><i class="sw5"></i><i class="sw6"></i></span><span class="shop-btn">SHOP NOW</span></div>
    <div class="product-card is-hover"><i class="can plum"></i><span class="p-title">Product Title</span><span class="p-price">$30.00</span><span class="swatches"><i class="sw1"></i><i class="sw2"></i><i class="sw3"></i><i class="sw4"></i><i class="sw5"></i><i class="sw6"></i></span><span class="shop-btn">SHOP NOW</span></div>
    <div class="product-card"><i class="can graphite"></i><span class="p-title">Product Title</span><span class="p-price">$30.00</span><span class="swatches"><i class="sw1"></i><i class="sw2"></i><i class="sw3"></i><i class="sw4"></i><i class="sw5"></i><i class="sw6"></i></span><span class="shop-btn">SHOP NOW</span></div>
  </div>
  <div class="quick-icons"><i></i><i></i><i></i></div>
  <span class="btn view-all">VIEW ALL PRODUCTS</span>
  <h2 class="sec-title" style="top:390px">HAIR THICKENING FIBRES <span class="hl">IN 3 EASY STEPS</span></h2>
  <div class="steps">
    <div class="step"><span class="step-num">01</span><span class="step-ring"><svg width="24" height="24" viewBox="0 0 24 24"><path d="M12 4C10 9 11 14 12 17" stroke="#fff" stroke-width="2" fill="none" stroke-linecap="round"/><path d="M3 19H21" stroke="#fff" stroke-width="1.2"/><circle cx="8" cy="21" r=".9" fill="#fff"/><circle cx="16" cy="21" r=".9" fill="#fff"/></svg></span><h3>Densora Hair Fibres</h3><p>Lorem ipsum dolor sit consectetur adipiscing elit, sed do eiusm tempor incididunt ut labore et dolore</p></div>
    <div class="step"><span class="step-num">02</span><span class="step-ring"><svg width="24" height="24" viewBox="0 0 24 24"><path d="M7 20C4 12 9 4 15 4C20 5 20 12 16 20" stroke="#fff" stroke-width="1.8" fill="none"/><path d="M10 19C8 13 11 8 14 8" stroke="#fff" stroke-width="1.4" fill="none"/></svg></span><h3>Densora Perfecting Tools</h3><p>Lorem ipsum dolor sit consectetur adipiscing elit, sed do eiusm tempor incididunt ut labore et dolore</p></div>
    <div class="step"><span class="step-num">03</span><span class="step-ring"><svg width="24" height="24" viewBox="0 0 24 24"><rect x="9" y="3" width="6" height="4" fill="#fff"/><path d="M15 4H19" stroke="#fff" stroke-width="1.4"/><rect x="10.5" y="7" width="3" height="4" fill="#fff"/><ellipse cx="12" cy="17" rx="5" ry="5.5" fill="#fff"/></svg></span><h3>Densora Fibrehold Spray</h3><p>Lorem ipsum dolor sit consectetur adipiscing elit, sed do eiusm tempor incididunt ut labore et dolore</p></div>
  </div>
  <h2 class="sec-title" style="top:537px">CONCEAL HAIR LOSS <span class="hl">WITH HAIR FIBRES</span></h2>
  <div class="videos">
    <div class="video-card"><span class="btn">WATCH OUR VIDEO</span><h3>Hair Fibres to Conceal<br><b>Thinning Hair</b></h3><div class="ba-labels"><span>Before</span><span>After</span></div><div class="ba-photo" role="img" aria-label="Before and after photos of a woman's thinning parting"></div></div>
    <div class="video-card"><span class="btn">WATCH OUR VIDEO</span><h3>Hair Fibres to Conceal<br><b>Thinning Hair</b></h3><div class="ba-labels"><span>Before</span><span>After</span></div><div class="ba-photo men" role="img" aria-label="Before and after photos of a man's thinning crown"></div></div>
  </div>
  <h2 class="abs about-title">ABOUT <span class="blue">US</span></h2>
  <p class="abs about-text">Lorem ipsum dolor sit amet, consectetur adipiscing elit, sed do eiusmod tempor incididunt ut labore et dolore magna aliqua. Ut enim ad minim veniam, quis nostrud exercitation ullamco laboris nisi ut aliquip ex ea commodo consequat. Lorem ipsum dolor sit amet, consectetur adipiscing elit, sed do eiusmod tempor incididunt ut labore et dolore magna aliqua. Ut enim ad minim veniam, quis nostrud exercitation ullamco laboris nisi ut aliquip ex ea commodo consequat. Lorem ipsum dolor sit amet, consectetur adipiscing elit, sed do eiusmod</p>
  <span class="btn learn-btn">LEARN MORE</span>
  <div class="abs about-photo" role="img" aria-label="Portrait photo of a woman with long voluminous curly hair"></div>
  <h2 class="sec-title" style="top:810px">TESTIMONIALS</h2>
  <div class="quotes">
    <p class="quote">Sed ut perspiciatis unde omnis istenatus error sit voluptatem accusandoloremque laudantium, totam aperiam</p>
    <p class="quote featured">Sed ut perspiciatis unde omnis istenatus error sit voluptatem accusandoloremque laudantium, totam aperiam</p>
    <p class="quote">Sed ut perspiciatis unde omnis istenatus error sit voluptatem accusandoloremque laudantium, totam aperiam</p>
  </div>
  <div class="authors">
    <div class="author"><span class="avatar" role="img" aria-label="Customer photo"></span><div><b>ALEX REED</b><small>Businessman</small></div></div>
    <div class="author"><span class="avatar" role="img" aria-label="Customer photo"></span><div><b>ALEX REED</b><small>Businessman</small></div></div>
    <div class="author"><span class="avatar" role="img" aria-label="Customer photo"></span><div><b>ALEX REED</b><small>Businessman</small></div></div>
  </div>
  <h2 class="sec-title" style="top:962px">THICKER HAIR IN 30 SECONDS</h2>
  <p class="abs thick-text">Sed ut perspiciatis unde omnis iste natus error sit voluptatem accusantium doloremque laudantium, totam rem aperiam, eaque ipsa quae ab illo inventore veritatis et quasi architecto beatae vitae dicta sunt explicabo. Nemo enim ipsam voluptatem quia voluptas sit aspernatur aut odit aut fugit, sed quia consequuntur</p>
  <div class="abs foot-logo"><b>DENSORA</b><small>HAIR BUILDING FIBRE</small></div>
  <div class="abs payments"><span>lumen split</span><i></i><span>tok fund</span><i></i><span>cards</span></div>
  <div class="foot-col col-links"><h4>QUICK LINKS</h4><ul><li>Home</li><li>About Us</li><li>Our Products</li><li>Gallery</li><li>Contact Us</li></ul></div>
  <div class="foot-col contact col-contact"><h4>CONTACT US</h4><ul><li>+61 400 555 010</li><li>info@densora.com</li><li>7 Harbour Lane, Westmere Australia</li><li><u>View Other Location</u></li></ul></div>
  <div class="foot-col col-subscribe"><h4>SUBSCRIBE NOW</h4><p>Sed ut perspiciatis unde omnis iste natus error sit voluptatem accusantium</p><div class="email-field"><span>Email Address</span><i></i></div><div class="socials"><i></i><i class="on"></i><i></i><i></i></div></div>
  <div class="copyright">© 2022 Densora. All Rights Reserved</div>
</section>

<!-- ===== Theme: light grey ===== -->
<section class="page page-2 theme-light">
  <svg class="page-shapes" viewBox="0 0 296 1121" aria-hidden="true">
    <rect y="518" width="296" height="155" fill="var(--band)"/>
    <rect y="941" width="296" height="90" fill="rgba(0,0,0,.05)"/>
    <path d="M0 0H296V150C200 152 90 172 0 210Z" fill="var(--navy)"/>
    <path d="M0 210C55 184 110 168 150 163" stroke="var(--blue)" stroke-width="2.4" fill="none"/>
    <path d="M0 388C100 386 220 362 296 330" stroke="var(--blue)" stroke-width="2" fill="none"/>
    <path d="M0 811C70 772 170 759 296 756" stroke="var(--blue)" stroke-width="2" fill="none"/>
    <path d="M0 1035C120 1030 230 1002 296 972V1121H0Z" fill="var(--navy)"/>
    <path d="M0 1035C120 1030 230 1002 296 972" stroke="var(--blue)" stroke-width="2" fill="none"/>
  </svg>
  <div class="topbar"><span>Spend $60 or more to receive free standard shipping</span><nav class="topbar-links"><span>Login</span><span>My Account</span><span>Checkout</span><span>Wishlist</span></nav></div>
  <header class="mainnav"><div class="logo"><b>DENSORA</b><small>HAIR BUILDING FIBRE</small></div><nav class="menu"><span class="active">Home</span><span>About</span><span>Shop</span><span>Offers</span><span>How It Works</span><span>FAQ</span><span>Contact</span></nav><span class="nav-icon search"></span><span class="nav-icon cart"></span></header>
  <div class="abs hero-photo" role="img" aria-label="Photo of a glamorous couple with full, thick hair"></div>
  <h1 class="abs hero-title">HAIR - BUILDING FIBRE<br>FOR <em>THICKER , FULLER</em><br>HAIR</h1>
  <p class="abs hero-text">Lorem ipsum dolor sit amet, consectetur adipiscing elit, sed do eiusmod tempor incididunt ut labore</p>
  <span class="btn hero-btn">PURCHASE NOW</span>
  <div class="abs hero-product" role="img" aria-label="Product shot of hair fibre bottles and spray"></div>
  <span class="abs best-badge"></span>
  <h2 class="sec-title" style="top:209px">FEATURED PRODUCTS</h2>
  <div class="products">
    <div class="product-card"><i class="can"></i><span class="p-title">Product Title</span><span class="p-price">$30.00</span><span class="swatches"><i class="sw1"></i><i class="sw2"></i><i class="sw3"></i><i class="sw4"></i><i class="sw5"></i><i class="sw6"></i></span><span class="shop-btn">SHOP NOW</span></div>
    <div class="product-card"><i class="can silver"></i><span class="p-title">Product Title</span><span class="p-price">$30.00</span><span class="swatches"><i class="sw1"></i><i class="sw2"></i><i class="sw3"></i><i class="sw4"></i><i class="sw5"></i><i class="sw6"></i></span><span class="shop-btn">SHOP NOW</span></div>
    <div class="product-card is-hover"><i class="can plum"></i><span class="p-title">Product Title</span><span class="p-price">$30.00</span><span class="swatches"><i class="sw1"></i><i class="sw2"></i><i class="sw3"></i><i class="sw4"></i><i class="sw5"></i><i class="sw6"></i></span><span class="shop-btn">SHOP NOW</span></div>
    <div class="product-card"><i class="can graphite"></i><span class="p-title">Product Title</span><span class="p-price">$30.00</span><span class="swatches"><i class="sw1"></i><i class="sw2"></i><i class="sw3"></i><i class="sw4"></i><i class="sw5"></i><i class="sw6"></i></span><span class="shop-btn">SHOP NOW</span></div>
  </div>
  <div class="quick-icons"><i></i><i></i><i></i></div>
  <span class="btn view-all">VIEW ALL PRODUCTS</span>
  <h2 class="sec-title" style="top:390px">HAIR THICKENING FIBRES IN 3 EASY STEPS</h2>
  <div class="steps">
    <div class="step"><span class="step-num">01</span><span class="step-ring"><svg width="24" height="24" viewBox="0 0 24 24"><path d="M12 4C10 9 11 14 12 17" stroke="#fff" stroke-width="2" fill="none" stroke-linecap="round"/><path d="M3 19H21" stroke="#fff" stroke-width="1.2"/><circle cx="8" cy="21" r=".9" fill="#fff"/><circle cx="16" cy="21" r=".9" fill="#fff"/></svg></span><h3>Densora Hair Fibres</h3><p>Lorem ipsum dolor sit consectetur adipiscing elit, sed do eiusm tempor incididunt ut labore et dolore</p></div>
    <div class="step"><span class="step-num">02</span><span class="step-ring"><svg width="24" height="24" viewBox="0 0 24 24"><path d="M7 20C4 12 9 4 15 4C20 5 20 12 16 20" stroke="#fff" stroke-width="1.8" fill="none"/><path d="M10 19C8 13 11 8 14 8" stroke="#fff" stroke-width="1.4" fill="none"/></svg></span><h3>Densora Perfecting Tools</h3><p>Lorem ipsum dolor sit consectetur adipiscing elit, sed do eiusm tempor incididunt ut labore et dolore</p></div>
    <div class="step"><span class="step-num">03</span><span class="step-ring"><svg width="24" height="24" viewBox="0 0 24 24"><rect x="9" y="3" width="6" height="4" fill="#fff"/><path d="M15 4H19" stroke="#fff" stroke-width="1.4"/><rect x="10.5" y="7" width="3" height="4" fill="#fff"/><ellipse cx="12" cy="17" rx="5" ry="5.5" fill="#fff"/></svg></span><h3>Densora Fibrehold Spray</h3><p>Lorem ipsum dolor sit consectetur adipiscing elit, sed do eiusm tempor incididunt ut labore et dolore</p></div>
  </div>
  <h2 class="sec-title" style="top:537px">CONCEAL HAIR LOSS WITH HAIR FIBRES</h2>
  <div class="videos">
    <div class="video-card"><span class="btn">WATCH OUR VIDEO</span><h3>Hair Fibres to Conceal<br><b>Thinning Hair</b></h3><div class="ba-labels"><span>Before</span><span>After</span></div><div class="ba-photo" role="img" aria-label="Before and after photos of a woman's thinning parting"></div></div>
    <div class="video-card"><span class="btn">WATCH OUR VIDEO</span><h3>Hair Fibres to Conceal<br><b>Thinning Hair</b></h3><div class="ba-labels"><span>Before</span><span>After</span></div><div class="ba-photo men" role="img" aria-label="Before and after photos of a man's thinning crown"></div></div>
  </div>
  <h2 class="abs about-title">ABOUT <span class="blue">US</span></h2>
  <p class="abs about-text">Lorem ipsum dolor sit amet, consectetur adipiscing elit, sed do eiusmod tempor incididunt ut labore et dolore magna aliqua. Ut enim ad minim veniam, quis nostrud exercitation ullamco laboris nisi ut aliquip ex ea commodo consequat. Lorem ipsum dolor sit amet, consectetur adipiscing elit, sed do eiusmod tempor incididunt ut labore et dolore magna aliqua. Ut enim ad minim veniam, quis nostrud exercitation ullamco laboris nisi ut aliquip ex ea commodo consequat. Lorem ipsum dolor sit amet, consectetur adipiscing elit, sed do eiusmod</p>
  <span class="btn learn-btn">LEARN MORE</span>
  <div class="abs about-photo" role="img" aria-label="Portrait photo of a woman with long voluminous curly hair"></div>
  <h2 class="sec-title" style="top:810px">TESTIMONIALS</h2>
  <div class="quotes">
    <p class="quote">Sed ut perspiciatis unde omnis istenatus error sit voluptatem accusandoloremque laudantium, totam aperiam</p>
    <p class="quote featured">Sed ut perspiciatis unde omnis istenatus error sit voluptatem accusandoloremque laudantium, totam aperiam</p>
    <p class="quote">Sed ut perspiciatis unde omnis istenatus error sit voluptatem accusandoloremque laudantium, totam aperiam</p>
  </div>
  <div class="authors">
    <div class="author"><span class="avatar" role="img" aria-label="Customer photo"></span><div><b>ALEX REED</b><small>Businessman</small></div></div>
    <div class="author"><span class="avatar" role="img" aria-label="Customer photo"></span><div><b>ALEX REED</b><small>Businessman</small></div></div>
    <div class="author"><span class="avatar" role="img" aria-label="Customer photo"></span><div><b>ALEX REED</b><small>Businessman</small></div></div>
  </div>
  <h2 class="sec-title" style="top:962px">THICKER HAIR IN 30 SECONDS</h2>
  <p class="abs thick-text">Sed ut perspiciatis unde omnis iste natus error sit voluptatem accusantium doloremque laudantium, totam rem aperiam, eaque ipsa quae ab illo inventore veritatis et quasi architecto beatae vitae dicta sunt explicabo. Nemo enim ipsam voluptatem quia voluptas sit aspernatur aut odit aut fugit, sed quia consequuntur</p>
  <div class="abs foot-logo"><b>DENSORA</b><small>HAIR BUILDING FIBRE</small></div>
  <div class="abs payments"><span>lumen split</span><i></i><span>tok fund</span><i></i><span>cards</span></div>
  <div class="foot-col col-links"><h4>QUICK LINKS</h4><ul><li>Home</li><li>About Us</li><li>Our Products</li><li>Gallery</li><li>Contact Us</li></ul></div>
  <div class="foot-col contact col-contact"><h4>CONTACT US</h4><ul><li>+61 400 555 010</li><li>info@densora.com</li><li>7 Harbour Lane, Westmere Australia</li><li><u>View Other Location</u></li></ul></div>
  <div class="foot-col col-subscribe"><h4>SUBSCRIBE NOW</h4><p>Sed ut perspiciatis unde omnis iste natus error sit voluptatem accusantium</p><div class="email-field"><span>Email Address</span><i></i></div><div class="socials"><i></i><i class="on"></i><i></i><i></i></div></div>
  <div class="copyright">© 2022 Densora. All Rights Reserved</div>
</section>

<!-- ===== Theme: gold ===== -->
<section class="page page-3 theme-gold">
  <svg class="page-shapes" viewBox="0 0 296 1121" aria-hidden="true">
    <rect y="518" width="296" height="155" fill="var(--band)"/>
    <rect y="941" width="296" height="90" fill="rgba(255,255,255,.06)"/>
    <path d="M0 0H296V150C200 152 90 172 0 210Z" fill="var(--navy)"/>
    <path d="M0 210C55 184 110 168 150 163" stroke="var(--blue)" stroke-width="2.4" fill="none"/>
    <path d="M0 388C100 386 220 362 296 330" stroke="var(--blue)" stroke-width="2" fill="none"/>
    <path d="M0 811C70 772 170 759 296 756" stroke="var(--blue)" stroke-width="2" fill="none"/>
    <path d="M0 1035C120 1030 230 1002 296 972V1121H0Z" fill="var(--navy)"/>
    <path d="M0 1035C120 1030 230 1002 296 972" stroke="var(--blue)" stroke-width="2" fill="none"/>
  </svg>
  <div class="topbar"><span>Spend $60 or more to receive free standard shipping</span><nav class="topbar-links"><span>Login</span><span>My Account</span><span>Checkout</span><span>Wishlist</span></nav></div>
  <header class="mainnav"><div class="logo"><b>DENSORA</b><small>HAIR BUILDING FIBRE</small></div><nav class="menu"><span class="active">Home</span><span>About</span><span>Shop</span><span>Offers</span><span>How It Works</span><span>FAQ</span><span>Contact</span></nav><span class="nav-icon search"></span><span class="nav-icon cart"></span></header>
  <div class="abs hero-photo" role="img" aria-label="Photo of a glamorous couple with full, thick hair"></div>
  <h1 class="abs hero-title">HAIR - BUILDING FIBRE<br>FOR <em>THICKER , FULLER</em><br>HAIR</h1>
  <p class="abs hero-text">Lorem ipsum dolor sit amet, consectetur adipiscing elit, sed do eiusmod tempor incididunt ut labore</p>
  <span class="btn hero-btn">PURCHASE NOW</span>
  <div class="abs hero-product" role="img" aria-label="Product shot of hair fibre bottles and spray"></div>
  <span class="abs best-badge"></span>
  <h2 class="sec-title" style="top:209px">FEATURED PRODUCTS</h2>
  <div class="products">
    <div class="product-card"><i class="can"></i><span class="p-title">Product Title</span><span class="p-price">$30.00</span><span class="swatches"><i class="sw1"></i><i class="sw2"></i><i class="sw3"></i><i class="sw4"></i><i class="sw5"></i><i class="sw6"></i></span><span class="shop-btn">SHOP NOW</span></div>
    <div class="product-card"><i class="can silver"></i><span class="p-title">Product Title</span><span class="p-price">$30.00</span><span class="swatches"><i class="sw1"></i><i class="sw2"></i><i class="sw3"></i><i class="sw4"></i><i class="sw5"></i><i class="sw6"></i></span><span class="shop-btn">SHOP NOW</span></div>
    <div class="product-card is-hover"><i class="can plum"></i><span class="p-title">Product Title</span><span class="p-price">$30.00</span><span class="swatches"><i class="sw1"></i><i class="sw2"></i><i class="sw3"></i><i class="sw4"></i><i class="sw5"></i><i class="sw6"></i></span><span class="shop-btn">SHOP NOW</span></div>
    <div class="product-card"><i class="can graphite"></i><span class="p-title">Product Title</span><span class="p-price">$30.00</span><span class="swatches"><i class="sw1"></i><i class="sw2"></i><i class="sw3"></i><i class="sw4"></i><i class="sw5"></i><i class="sw6"></i></span><span class="shop-btn">SHOP NOW</span></div>
  </div>
  <div class="quick-icons"><i></i><i></i><i></i></div>
  <span class="btn view-all">VIEW ALL PRODUCTS</span>
  <h2 class="sec-title" style="top:390px">HAIR THICKENING FIBRES IN 3 EASY STEPS</h2>
  <div class="steps">
    <div class="step"><span class="step-num">01</span><span class="step-ring"><svg width="24" height="24" viewBox="0 0 24 24"><path d="M12 4C10 9 11 14 12 17" stroke="#fff" stroke-width="2" fill="none" stroke-linecap="round"/><path d="M3 19H21" stroke="#fff" stroke-width="1.2"/><circle cx="8" cy="21" r=".9" fill="#fff"/><circle cx="16" cy="21" r=".9" fill="#fff"/></svg></span><h3>Densora Hair Fibres</h3><p>Lorem ipsum dolor sit consectetur adipiscing elit, sed do eiusm tempor incididunt ut labore et dolore</p></div>
    <div class="step"><span class="step-num">02</span><span class="step-ring"><svg width="24" height="24" viewBox="0 0 24 24"><path d="M7 20C4 12 9 4 15 4C20 5 20 12 16 20" stroke="#fff" stroke-width="1.8" fill="none"/><path d="M10 19C8 13 11 8 14 8" stroke="#fff" stroke-width="1.4" fill="none"/></svg></span><h3>Densora Perfecting Tools</h3><p>Lorem ipsum dolor sit consectetur adipiscing elit, sed do eiusm tempor incididunt ut labore et dolore</p></div>
    <div class="step"><span class="step-num">03</span><span class="step-ring"><svg width="24" height="24" viewBox="0 0 24 24"><rect x="9" y="3" width="6" height="4" fill="#fff"/><path d="M15 4H19" stroke="#fff" stroke-width="1.4"/><rect x="10.5" y="7" width="3" height="4" fill="#fff"/><ellipse cx="12" cy="17" rx="5" ry="5.5" fill="#fff"/></svg></span><h3>Densora Fibrehold Spray</h3><p>Lorem ipsum dolor sit consectetur adipiscing elit, sed do eiusm tempor incididunt ut labore et dolore</p></div>
  </div>
  <h2 class="sec-title" style="top:537px">CONCEAL HAIR LOSS WITH HAIR FIBRES</h2>
  <div class="videos">
    <div class="video-card"><span class="btn">WATCH OUR VIDEO</span><h3>Hair Fibres to Conceal<br><b>Thinning Hair</b></h3><div class="ba-labels"><span>Before</span><span>After</span></div><div class="ba-photo" role="img" aria-label="Before and after photos of a woman's thinning parting"></div></div>
    <div class="video-card"><span class="btn">WATCH OUR VIDEO</span><h3>Hair Fibres to Conceal<br><b>Thinning Hair</b></h3><div class="ba-labels"><span>Before</span><span>After</span></div><div class="ba-photo men" role="img" aria-label="Before and after photos of a man's thinning crown"></div></div>
  </div>
  <h2 class="abs about-title">ABOUT <span class="blue">US</span></h2>
  <p class="abs about-text">Lorem ipsum dolor sit amet, consectetur adipiscing elit, sed do eiusmod tempor incididunt ut labore et dolore magna aliqua. Ut enim ad minim veniam, quis nostrud exercitation ullamco laboris nisi ut aliquip ex ea commodo consequat. Lorem ipsum dolor sit amet, consectetur adipiscing elit, sed do eiusmod tempor incididunt ut labore et dolore magna aliqua. Ut enim ad minim veniam, quis nostrud exercitation ullamco laboris nisi ut aliquip ex ea commodo consequat. Lorem ipsum dolor sit amet, consectetur adipiscing elit, sed do eiusmod</p>
  <span class="btn learn-btn">LEARN MORE</span>
  <div class="abs about-photo" role="img" aria-label="Portrait photo of a woman with long voluminous curly hair"></div>
  <h2 class="sec-title" style="top:810px">TESTIMONIALS</h2>
  <div class="quotes">
    <p class="quote">Sed ut perspiciatis unde omnis istenatus error sit voluptatem accusandoloremque laudantium, totam aperiam</p>
    <p class="quote featured">Sed ut perspiciatis unde omnis istenatus error sit voluptatem accusandoloremque laudantium, totam aperiam</p>
    <p class="quote">Sed ut perspiciatis unde omnis istenatus error sit voluptatem accusandoloremque laudantium, totam aperiam</p>
  </div>
  <div class="authors">
    <div class="author"><span class="avatar" role="img" aria-label="Customer photo"></span><div><b>ALEX REED</b><small>Businessman</small></div></div>
    <div class="author"><span class="avatar" role="img" aria-label="Customer photo"></span><div><b>ALEX REED</b><small>Businessman</small></div></div>
    <div class="author"><span class="avatar" role="img" aria-label="Customer photo"></span><div><b>ALEX REED</b><small>Businessman</small></div></div>
  </div>
  <h2 class="sec-title" style="top:962px">THICKER HAIR IN 30 SECONDS</h2>
  <p class="abs thick-text">Sed ut perspiciatis unde omnis iste natus error sit voluptatem accusantium doloremque laudantium, totam rem aperiam, eaque ipsa quae ab illo inventore veritatis et quasi architecto beatae vitae dicta sunt explicabo. Nemo enim ipsam voluptatem quia voluptas sit aspernatur aut odit aut fugit, sed quia consequuntur</p>
  <div class="abs foot-logo"><b>DENSORA</b><small>HAIR BUILDING FIBRE</small></div>
  <div class="abs payments"><span>lumen split</span><i></i><span>tok fund</span><i></i><span>cards</span></div>
  <div class="foot-col col-links"><h4>QUICK LINKS</h4><ul><li>Home</li><li>About Us</li><li>Our Products</li><li>Gallery</li><li>Contact Us</li></ul></div>
  <div class="foot-col contact col-contact"><h4>CONTACT US</h4><ul><li>+61 400 555 010</li><li>info@densora.com</li><li>7 Harbour Lane, Westmere Australia</li><li><u>View Other Location</u></li></ul></div>
  <div class="foot-col col-subscribe"><h4>SUBSCRIBE NOW</h4><p>Sed ut perspiciatis unde omnis iste natus error sit voluptatem accusantium</p><div class="email-field"><span>Email Address</span><i></i></div><div class="socials"><i></i><i class="on"></i><i></i><i></i></div></div>
  <div class="copyright">© 2022 Densora. All Rights Reserved</div>
</section>

</main>
</body>
</html>
```